Bright and beautiful business card for a coach

I'm a personal and business coach based in Perth, Australia. I need a business card that whilst subtle and elegant, will stand out and appeal on a table full of cards.

My business name is Fern Mentoring and the business card must represent the warmth and brightness implied in the name, without being gimmicky. It must have a warmth and appeal and be easy to read.

I prefer clean, minimalist designs.

It must align with the feel of my website and socials: https://www.fernmentoring-example.com.au/
https://www.instagram.com/fernmentoringau/
https://www.facebook.com/fernmentoringau
Updates

Hi Designers Thank you so much for taking the time to submit designs. I wonder if I could have explained myself a little better. Most of the designs that have been submitted look rather formal and many have quite corporate looking embellishments on them (to my eye). I would like softer, warmer, more organic. I’m open to people playing about and being more abstract, using softer embellishments (e.g the line drawing flowers and grasses I’ve used in my socials) incorporating other colours from my palette or like the social icons in my email signature (in PDF), perhaps playing with size/oversize, playing with the bleed. Please don’t be constrained by what I’ve already done, it merely needs to compliment. I’m sorry if I’m not using the right words or have led you astray. I’m no designer, but I’ve done my website, socials, email signature etc all myself (my logo was a design contest) and I was really hoping for my business card to be something more creative than I could have made with a template. Reminder: No black cards/sides please. Thank you 😊

Target Market(s)

Individuals, most likely but not all female. Creative thinkers. Likely professionals.

Industry/Entity Type

Business & Personal Coach

Contact Information for Business Card

(Fern Mentoring Logo) Name: Greta Pellham; Title: Business & Personal Coach; Phone number: +61 (0)458 913307; Email: greta@fernmentoring-example.com.au; Website: https://fernmentoring-example.com.au; Social icons for Facebook, Instagram & LinkedIn: @fernmentoringAU. Optional strapline: "A thinking partner to help you cut through the noise"

Font styles to use
Sans Serif

Colors
00AB8E
00BBA5
67D7C9
C6EFE9
E9F9F6
59FF00
82FF00
B8FF75
E3FFCB
F4FFEA
FFC000
F8CF3A
FAE287
FDF2CF
FEFAEE

Requirements
Must have
• Must align with feel of my website and socials. Must have a pop of #FFC000 (possibly whole of one side, or at least a block). Bright or white background. Easy to read.
Nice to have
• Possibly incorporate the sunshine/grass picture I have used in website and socials - will upload.
Should not have
• Must not be black or dark. Not impersonal or corporate looking.

```html
<!DOCTYPE html>
<html lang="en">
<head>
<meta charset="utf-8">
<title>Fern Mentoring – Business Card</title>
<link href="https://fonts.googleapis.com/css2?family=Poppins:wght@400;500;600&display=swap" rel="stylesheet">
<style>
  :root {
    --page-bg: #d9dadc;
    --card-light: #fefaee;
    --gold: #ffc000;
    --gold-deep: #e0951a;
    --gold-text: #d98a0e;
    --ink: #3a3b3d;
    --ink-soft: #55575a;
    --logo-gold: #d99a1c;
    --grass-light: #f4f6ef;
    --grass-mid: #dfe6d2;
    --grass-deep: #c9d4b8;
  }
  * { box-sizing: border-box; margin: 0; padding: 0; }
  html, body {
    width: 1200px; height: 800px; overflow: hidden;
    background: var(--page-bg);
    font-family: "Poppins", sans-serif;
  }
  .sheet {
    width: 1200px; height: 800px;
    display: flex; align-items: center; justify-content: center; gap: 40px;
  }
  .card {
    position: relative;
    width: 540px; height: 310px;
    border-radius: 18px; overflow: hidden;
    box-shadow: 0 10px 24px rgba(0,0,0,0.18);
  }

  /* Contact side */
  .card--contact { background: var(--card-light); }
  .card__wave { position: absolute; inset: 0; width: 100%; height: 100%; }
  .contact {
    position: absolute; left: 34px; top: 100px;
    color: var(--ink-soft);
  }
  .contact__name {
    font-size: 27px; font-weight: 600; color: var(--gold-text);
    line-height: 1.1;
  }
  .contact__title { font-size: 13.5px; margin: 3px 0 12px; color: var(--ink); }
  .contact__list { list-style: none; }
  .contact__item {
    display: flex; align-items: center; gap: 8px;
    font-size: 13.5px; line-height: 1.5;
  }
  .contact__icon { width: 12px; height: 12px; flex: none; }
  .social {
    position: absolute; right: 30px; bottom: 26px;
    display: flex; align-items: center; gap: 4px;
    font-size: 13px; font-weight: 500; color: var(--ink);
  }
  .social__dot {
    width: 13px; height: 13px; border-radius: 50%;
    background: var(--ink);
  }
  .social__handle { margin-left: 4px; }

  /* Brand side */
  .card--brand { background: var(--grass-light); }
  .brand__photo {
    position: absolute; inset: 0;
    background:
      radial-gradient(circle at 62% 18%, rgba(255,255,255,0.95) 0 8%, rgba(255,255,255,0) 38%),
      linear-gradient(180deg, var(--grass-light) 0%, var(--grass-mid) 55%, var(--grass-deep) 100%);
    opacity: 0.85;
  }
  .brand__veil { position: absolute; inset: 0; background: rgba(255,255,255,0.45); }
  .brand__logo {
    position: absolute; left: 0; right: 0; top: 108px;
    text-align: center;
    font-size: 38px; font-weight: 500; color: var(--logo-gold);
    letter-spacing: 1px;
  }
  .brand__strapline {
    position: absolute; left: 0; right: 0; bottom: 52px;
    text-align: center;
    font-size: 14px; color: var(--ink);
  }
</style>
</head>
<body>
<main class="sheet">

  <section class="card card--contact" aria-label="Card contact side">
    <svg class="card__wave" viewBox="0 0 540 310" preserveAspectRatio="none" aria-hidden="true">
      <path d="M214 310 C236 300 232 276 262 268 C318 254 372 214 410 148 C446 86 488 38 540 22 L540 310 Z" fill="var(--gold-deep)"/>
      <path d="M226 310 C248 302 246 284 274 278 C332 266 388 226 424 162 C458 102 496 58 540 44 L540 310 Z" fill="var(--gold)"/>
    </svg>
    <div class="contact">
      <h1 class="contact__name">Greta Pellham</h1>
      <p class="contact__title">Business &amp; Personal Coach</p>
      <ul class="contact__list">
        <li class="contact__item">
          <svg class="contact__icon" viewBox="0 0 24 24"><path fill="var(--gold-text)" d="M6.6 10.8a15 15 0 0 0 6.6 6.6l2.2-2.2c.3-.3.7-.4 1-.2 1.1.4 2.3.6 3.6.6.6 0 1 .4 1 1V20c0 .6-.4 1-1 1A17 17 0 0 1 3 4c0-.6.4-1 1-1h3.5c.6 0 1 .4 1 1 0 1.3.2 2.5.6 3.6.1.3 0 .7-.2 1z"/></svg>
          +61 (0)458 913307
        </li>
        <li class="contact__item">
          <svg class="contact__icon" viewBox="0 0 24 24"><rect x="2" y="5" width="20" height="14" rx="2" fill="var(--gold-text)"/><path d="M3 6l9 7 9-7" fill="none" stroke="var(--card-light)" stroke-width="2"/></svg>
          greta@fernmentoring-example.com.au
        </li>
        <li class="contact__item">
          <svg class="contact__icon" viewBox="0 0 24 24"><circle cx="12" cy="12" r="10" fill="var(--gold-text)"/><path d="M2 12h20M12 2c3 3 3 17 0 20M12 2c-3 3-3 17 0 20" fill="none" stroke="var(--card-light)" stroke-width="1.6"/></svg>
          fernmentoring-example.com.au
        </li>
      </ul>
    </div>
    <div class="social">
      <span class="social__dot"></span>
      <span class="social__dot"></span>
      <span class="social__dot"></span>
      <span class="social__handle">@fernmentoringAU</span>
    </div>
  </section>

  <section class="card card--brand" aria-label="Card brand side">
    <div class="brand__photo" role="img" aria-label="Soft sunlit grass photograph"></div>
    <div class="brand__veil"></div>
    <p class="brand__logo">Fern Mentoring</p>
    <p class="brand__strapline">A thinking partner to help you cut through the noise</p>
  </section>

</main>
</body>
</html>
```